One piece Trade show banner, 8' x 8' square

One piece banner for trade show
8' x 8' airborne geophysical company

Target Market(s)

Business

Industry/Entity Type

mineral exploration and science

Colors
0054AA
0677BA
7BADD7
CADEEF
E8F1F8
FFC000
F8CF3A
FAE287
FDF2CF
FEFAEE

Requirements
Must have
• Company logo (attached), slogan (Airborne Geophysics for Discovery). We are looking for a new banner, for a standard 8 x 8' square one-piece booth. I have attached some pictures, our logo, our old banner for reference, and two examples from unrelated companies from a tradeshow that we like. If its possible I'd like to change the color of the helicopter from green to dark grey. IE, keep the orange and white, just change green to dark grey. Looking for a simple, clean design with minimal text.
Nice to have
• I have attached examples of banners that we like (2xIMG), plus our old 3-piece banner r.
Should not have
• Green in the helicopter. Please change the color of the helicopter with green/orange/white to dark grey/orange/white. IE change the green to dark grey and leave the orange and white alone. I've attached lots of pictures but I don't expect them all to be used.

```html
<!DOCTYPE html>
<html lang="en">
<head>
<meta charset="utf-8">
<title>Airborne Geophysics for Discovery – Trade Show Banner</title>
<link rel="stylesheet" href="https://fonts.googleapis.com/css2?family=Oswald:wght@700&display=swap">
<style>
  :root {
    --page: #ffffff;
    --charcoal: #2b2b2b;
    --gold: #fbc02d;
    --white: #ffffff;
    --sky: #b9cfdc;
    --ridge: #3f7f8c;
    --forest: #2f6a6a;
    --rock: #52605a;
  }
  html, body {
    margin: 0;
    width: 1200px;
    height: 1200px;
    overflow: hidden;
    background: var(--page);
  }
  .banner {
    position: absolute;
    left: 124px;
    top: 124px;
    width: 952px;
    height: 952px;
  }
  .banner svg { display: block; }
  .headline {
    font-family: "Oswald", "Arial Narrow", sans-serif;
    font-weight: 700;
    fill: var(--white);
    filter: url(#text-shadow);
  }
  .headline--accent { fill: var(--gold); }
  .brand-name {
    font-family: "Oswald", "Arial Narrow", sans-serif;
    font-weight: 700;
    fill: var(--white);
    letter-spacing: 2px;
  }
  .rule { stroke: var(--gold); stroke-width: 2; }
</style>
</head>
<body>
<div class="banner">
  <svg width="952" height="952" viewBox="0 0 952 952" xmlns="http://www.w3.org/2000/svg">
    <defs>
      <linearGradient id="scene-tone" x1="0" y1="0" x2="0.35" y2="1">
        <stop offset="0" stop-color="var(--sky)"/>
        <stop offset="0.28" stop-color="#9fbccb"/>
        <stop offset="0.42" stop-color="var(--ridge)"/>
        <stop offset="0.75" stop-color="var(--forest)"/>
        <stop offset="1" stop-color="var(--rock)"/>
      </linearGradient>
      <filter id="text-shadow" x="-5%" y="-10%" width="110%" height="130%">
        <feDropShadow dx="3" dy="4" stdDeviation="2" flood-color="#000" flood-opacity="0.6"/>
      </filter>
    </defs>

    <rect class="panel" width="952" height="952" fill="var(--charcoal)"/>

    <path class="swoosh" fill="var(--gold)"
      d="M0,0 L271,0 C205,45 160,110 172,180 C185,260 260,340 350,430
         C450,530 580,620 575,790 C572,860 555,910 540,952 L0,952 Z"/>

    <path class="photo-area" role="img"
      aria-label="Photo: white and orange survey helicopter with sensor booms flying past forested mountain slopes"
      fill="url(#scene-tone)"
      d="M0,0 L216,0 C150,50 115,110 122,175 C130,260 200,340 300,430
         C410,530 555,630 548,790 C545,860 535,910 522,952 L0,952 Z"/>

    <line class="rule" x1="354" y1="81" x2="895" y2="81"/>

    <text class="headline" x="895" y="248" text-anchor="end"
      font-size="170" textLength="572" lengthAdjust="spacingAndGlyphs">AIRBORNE</text>
    <text class="headline" x="895" y="342" text-anchor="end"
      font-size="92" textLength="572" lengthAdjust="spacingAndGlyphs">GEOPHYSICS FOR</text>
    <text class="headline headline--accent" x="895" y="456" text-anchor="end"
      font-size="120" textLength="457" lengthAdjust="spacingAndGlyphs">DISCOVERY</text>

    <text class="brand-name" x="895" y="872" text-anchor="end" font-size="50">ALTUS AERIAL</text>
  </svg>
</div>
</body>
</html>
```